Redesign of LumoWordfind.com in Bootstrap 4

Current design of LumoWordfind.com is not responsive. We need to change it to latest version of Bootstrap 4 keeping essential elements in place.

Apart from home page, we need designs for http://www.lumowordfind.com/meaning/cat also.

Coding

Number of Pages Required

2 page

Colors
34a7d8

Requirements
Must have
• Bootstrap 4

```html
<!DOCTYPE html>
<html lang="en">
<head>
<meta charset="utf-8">
<title>LumoWordfind – English Dictionary</title>
<link href="https://fonts.googleapis.com/css2?family=Open+Sans:wght@400;600;700&family=Raleway:wght@400;500;600&display=swap" rel="stylesheet">
<style>
:root{
  --brand:#34a7d8;
  --brand-dark:#2b8fc0;
  --footer:#35a3d6;
  --footer-bar:#2c8fc4;
  --orange:#f39c12;
  --orange-dark:#e8870a;
  --text:#555;
  --muted:#777;
  --gray-band:#ececec;
  --white:#fff;
}
*{box-sizing:border-box;margin:0;padding:0}
html,body{width:699px;height:1200px;overflow:hidden}
body{font-family:"Open Sans",Arial,sans-serif;color:var(--text);background:var(--white);position:relative}
.abs{position:absolute}
.btn-orange{position:absolute;background:linear-gradient(var(--orange),var(--orange-dark));color:var(--white);font-weight:700;display:flex;align-items:center;justify-content:center;border-radius:2px;text-transform:uppercase}

/* header */
.site-header{position:absolute;left:0;top:0;width:699px;height:53px;background:var(--white)}
.brand{position:absolute;left:58px;top:14px;display:flex;align-items:center;gap:5px;font-family:"Raleway",sans-serif;font-weight:600;font-size:15px;color:var(--brand)}
.brand-dot{width:12px;height:12px;border-radius:50%;background:var(--orange)}
.main-nav a{position:absolute;top:24px;font-size:7px;color:#444;text-decoration:none;letter-spacing:.1px}
.login{left:590px;top:18px;width:52px;height:19px;font-size:7px;font-weight:600;justify-content:flex-start;padding-left:8px}
.login::after{content:"";position:absolute;right:8px;top:7px;width:3px;height:3px;border-right:1px solid #fff;border-bottom:1px solid #fff;transform:rotate(45deg)}

/* hero */
.hero{position:absolute;left:0;top:53px;width:699px;height:299px;background:linear-gradient(100deg,#8a8a8a 0%,#a9a9a9 40%,#b8b8b8 70%,#9a9a9a 100%)}
.hero-figure{position:absolute;right:0;top:0;width:390px;height:299px;background:radial-gradient(ellipse at 65% 55%,rgba(70,90,120,.55),rgba(160,160,160,0) 65%)}
.search-panel{position:absolute;left:43px;top:90px;width:385px;height:116px;background:rgba(255,255,255,.72);border:2px solid rgba(255,255,255,.85);border-radius:3px}
.search-title{position:absolute;left:0;width:100%;top:24px;text-align:center;font-family:"Raleway",sans-serif;font-weight:600;font-size:19px;color:var(--brand)}
.search-input{position:absolute;left:18px;top:55px;width:268px;height:25px;background:var(--white);border:1px solid #ddd;font-size:8px;color:#888;padding:8px 10px}
.search-btn{left:286px;top:55px;width:77px;height:25px;font-size:8.5px;gap:4px}
.search-hint{position:absolute;left:26px;top:90px;font-size:6.5px;color:#555}
.dots{position:absolute;left:335px;top:282px;display:flex;gap:4px}
.dots span{width:5px;height:5px;border-radius:50%;background:var(--white)}
.dots span:first-child{background:var(--orange)}

/* features */
.feature-art{position:absolute;left:115px;top:388px;width:140px;height:204px;background:radial-gradient(ellipse at 50% 55%,#e8e8e8,#f7f7f7 60%,#fff 80%)}
.feature-title{position:absolute;left:316px;top:410px;font-family:"Raleway",sans-serif;font-size:17px;color:var(--brand)}
.feature-list{position:absolute;left:318px;top:443px;list-style:none}
.feature-list li{display:flex;align-items:center;gap:7px;font-size:7.5px;color:#444;height:18.5px}
.get-free{left:320px;top:543px;width:90px;height:27px;font-size:8.5px}

/* gray band */
.tools{position:absolute;left:0;top:626px;width:699px;height:328px;background:var(--gray-band)}
.tool{position:absolute;width:260px}
.tool-icon{position:absolute;left:0;top:0}
.tool h3{position:absolute;top:4px;font-weight:400;font-size:9.5px;color:var(--brand)}
.tool p{position:absolute;top:24px;width:215px;font-size:6.2px;line-height:14px;color:var(--muted)}
.tool .btn-orange{width:64px;height:21px;font-size:5.8px;top:86px}

/* browse */
.browse-title{position:absolute;left:0;width:699px;top:986px;text-align:center;font-family:"Raleway",sans-serif;font-size:17px;color:#444}
.alphabet{position:absolute;left:137px;top:1019px;display:flex;gap:0;background:#eef3f7;padding:1px}
.alphabet a{width:16.3px;height:16px;margin-right:.5px;border:1px solid #8fc4e0;background:var(--white);font-size:7.5px;color:#333;text-decoration:none;display:flex;align-items:center;justify-content:center}

/* footer */
.site-footer{position:absolute;left:0;top:1074px;width:699px;height:101px;background:var(--footer);color:var(--white)}
.footer-col{position:absolute;top:24px}
.footer-col h4{font-family:"Raleway",sans-serif;font-weight:500;font-size:10px;margin-bottom:7px}
.footer-col ul{list-style:none}
.footer-col li{font-size:6.5px;line-height:12.5px}
.social{display:flex;gap:5px;margin-top:8px}
.social span{width:17px;height:17px;border-radius:50%;background:var(--white)}
.footer-bar{position:absolute;left:0;top:1175px;width:699px;height:25px;background:var(--footer-bar);color:var(--white);font-size:6.5px;display:flex;align-items:center;justify-content:center}
</style>
</head>
<body>

<header class="site-header">
  <div class="brand"><span class="brand-dot"></span>LumoWordfind</div>
  <nav class="main-nav">
    <a style="left:213px">HOME</a>
    <a style="left:266px">IDIOMS</a>
    <a style="left:322px">COMMON ERRORS</a>
    <a style="left:413px">CROSSWORD</a>
    <a style="left:489px">BLOG</a>
    <a style="left:540px">CONTACT</a>
  </nav>
  <div class="btn-orange login">LOGIN</div>
</header>

<section class="hero" role="img" aria-label="Grey concrete wall with faint scattered letters and a young man sitting on the floor working on a laptop">
  <div class="hero-figure"></div>
  <div class="search-panel">
    <h1 class="search-title">LUMO ENGLISH DICTIONARY</h1>
    <div class="search-input">Enter a word or phrase</div>
    <div class="btn-orange search-btn">
      <svg width="9" height="9" viewBox="0 0 10 10"><circle cx="4" cy="4" r="3" fill="none" stroke="#fff" stroke-width="1.4"/><line x1="6.2" y1="6.2" x2="9" y2="9" stroke="#fff" stroke-width="1.4"/></svg>SEARCH
    </div>
    <div class="search-hint">(eg. butterfly, essay, synonym)</div>
  </div>
  <div class="dots"><span></span><span></span><span></span><span></span></div>
</section>

<section class="features">
  <div class="feature-art" role="img" aria-label="3D white figure at a desk reading a book with a magnifying glass"></div>
  <h2 class="feature-title">Search, Save and Master Words</h2>
  <ul class="feature-list">
    <li><svg width="8" height="8" viewBox="0 0 8 8"><rect x=".5" y=".5" width="7" height="7" fill="none" stroke="#f39c12"/><path d="M2 4l1.5 1.5L6.5 2" fill="none" stroke="#f39c12" stroke-width="1.2"/></svg>Search from more than 300,000 words and phrases</li>
    <li><svg width="8" height="8" viewBox="0 0 8 8"><rect x=".5" y=".5" width="7" height="7" fill="none" stroke="#f39c12"/><path d="M2 4l1.5 1.5L6.5 2" fill="none" stroke="#f39c12" stroke-width="1.2"/></svg>Multiple usages to clarify the context</li>
    <li><svg width="8" height="8" viewBox="0 0 8 8"><rect x=".5" y=".5" width="7" height="7" fill="none" stroke="#f39c12"/><path d="M2 4l1.5 1.5L6.5 2" fill="none" stroke="#f39c12" stroke-width="1.2"/></svg>Audio, phonetics, meanings, synonyms and antonyms</li>
    <li><svg width="8" height="8" viewBox="0 0 8 8"><rect x=".5" y=".5" width="7" height="7" fill="none" stroke="#f39c12"/><path d="M2 4l1.5 1.5L6.5 2" fill="none" stroke="#f39c12" stroke-width="1.2"/></svg>Save the words to your personal deck and access from anywhere</li>
    <li><svg width="8" height="8" viewBox="0 0 8 8"><rect x=".5" y=".5" width="7" height="7" fill="none" stroke="#f39c12"/><path d="M2 4l1.5 1.5L6.5 2" fill="none" stroke="#f39c12" stroke-width="1.2"/></svg>It's FREE</li>
  </ul>
  <div class="btn-orange get-free">GET IT FREE!</div>
</section>

<section class="tools">
  <div class="tool" style="left:58px;top:41px">
    <svg class="tool-icon" width="42" height="38" viewBox="0 0 42 38"><path d="M4 3h18l6 6v26H4z" fill="none" stroke="#333" stroke-width="2"/><line x1="9" y1="14" x2="22" y2="14" stroke="#333" stroke-width="2"/><line x1="9" y1="20" x2="22" y2="20" stroke="#333" stroke-width="2"/><line x1="9" y1="26" x2="18" y2="26" stroke="#333" stroke-width="2"/><path d="M24 32l12-16 3 2-12 16-4 1z" fill="#e74c3c"/></svg>
    <h3 style="left:51px">English Tidbit</h3>
    <p style="left:51px">To "gibe" is to taunt. Gibe is however slowly going out of use. Jibe means to agree but is often used in the negative sense. Although the versions of the tricksters jibed, the police officer suspected that there was something wrong.</p>
    <div class="btn-orange" style="left:50px">CLICK HERE</div>
  </div>
  <div class="tool" style="left:380px;top:41px">
    <svg class="tool-icon" width="36" height="38" viewBox="0 0 36 38"><path d="M3 6h20v28H3z" fill="none" stroke="#34a7d8" stroke-width="2"/><line x1="8" y1="14" x2="18" y2="14" stroke="#34a7d8" stroke-width="2"/><line x1="8" y1="20" x2="18" y2="20" stroke="#34a7d8" stroke-width="2"/><path d="M16 24l12-14 3 3-12 14-4 1z" fill="#34a7d8"/></svg>
    <h3 style="left:45px">Daily Crossword</h3>
    <p style="left:45px">To "gibe" is to taunt. Gibe is however slowly going out of use. Jibe means to agree but is often used in the negative sense. Although the versions of the tricksters jibed, the police officer suspected that there was something wrong.</p>
    <div class="btn-orange" style="left:44px">CLICK HERE</div>
  </div>
  <div class="tool" style="left:58px;top:181px">
    <svg class="tool-icon" width="38" height="38" viewBox="0 0 38 38"><circle cx="19" cy="19" r="17" fill="#f39c12"/><circle cx="19" cy="19" r="9" fill="#fbc36a"/></svg>
    <h3 style="left:47px">Emberfox Addon</h3>
    <p style="left:47px">To "gibe" is to taunt. Gibe is however slowly going out of use. Jibe means to agree but is often used in the negative sense. Although the versions of the tricksters jibed, the police officer suspected that there was something wrong.</p>
    <div class="btn-orange" style="left:46px">CLICK HERE</div>
  </div>
  <div class="tool" style="left:386px;top:181px">
    <svg class="tool-icon" width="36" height="40" viewBox="0 0 36 40"><rect x="3" y="2" width="17" height="34" rx="3" fill="none" stroke="#e74c3c" stroke-width="2.4"/><circle cx="11.5" cy="31" r="1.6" fill="#e74c3c"/><circle cx="24" cy="14" r="5" fill="none" stroke="#e74c3c" stroke-width="3" stroke-dasharray="2.5 1.5"/></svg>
    <h3 style="left:39px">Designed for Nimbus Phone</h3>
    <p style="left:39px">To "gibe" is to taunt. Gibe is however slowly going out of use. Jibe means to agree but is often used in the negative sense. Although the versions of the tricksters jibed, the police officer suspected that there was something wrong.</p>
    <div class="btn-orange" style="left:38px">CLICK HERE</div>
  </div>
</section>

<h2 class="browse-title">Browse Dictionary</h2>
<nav class="alphabet">
  <a>A</a><a>B</a><a>C</a><a>D</a><a>E</a><a>F</a><a>G</a><a>H</a><a>I</a><a>J</a><a>K</a><a>L</a><a>M</a><a>N</a><a>O</a><a>P</a><a>Q</a><a>R</a><a>S</a><a>T</a><a>U</a><a>V</a><a>W</a><a>X</a><a>Y</a><a>Z</a>
</nav>

<footer class="site-footer">
  <div class="footer-col" style="left:58px">
    <h4>LumoWordfind.com</h4>
    <ul style="float:left;width:80px"><li>Home</li><li>Idioms</li><li>Common Errors</li></ul>
    <ul style="float:left"><li>Crossword</li><li>Blog</li><li>Contact</li></ul>
  </div>
  <div class="footer-col" style="left:232px">
    <h4>Legal</h4>
    <ul><li>Privacy Policy</li><li>Terms of Use</li><li>Disclaimer</li></ul>
  </div>
  <div class="footer-col" style="left:343px">
    <h4>Others</h4>
    <ul><li>Popular Words</li><li>Common Errors in English</li><li>Exam Prep Online</li></ul>
  </div>
  <div class="footer-col" style="left:488px">
    <h4>Follow Us</h4>
    <ul><li>Connect with our social network</li></ul>
    <div class="social"><span></span><span></span><span></span><span></span><span></span></div>
  </div>
</footer>
<div class="footer-bar">Copyright © 2016. LumoWordfind. All rights reserved.</div>

</body>
</html>
```